Business Card Design - Photographer

I am a landscape photographer and I require a business card design. 

I require two designs:
1)  a double sided business card
 and
b)  a single sided business card 

The single sided design can either be the same as the double sided (with just one side having all the information)....or it can be an entire new design. Its up to you.

My corporate colours are (CMYK):

Blue   69, 32, 0, 0
Grey  72,  64,  47,  31
Green  32,  2,  91,  0
Yellow   0, 19, 92, 0
Orange  0, 39, 75, 0

Colour space in final file should be in CMYK.

The details that need to be included on the card:

- Use the provided Logo
- Name: Wiktor Baranowski
- Email:   sales@vistalumeworks.com.au
- Website:    vistalumeworks.com.au
- Twitter:    twitter.com/vistalumeworks
- Facebook:   facebook.com/vistalumeworks
- Mobile  0417 539 662

Please use the attached template to design the logo to the specified size, including the marked bleed lines. I have also attached my logo in PNG (transparent background) and ai format for you to use.

The final file should be:
- Photoshop version with layers so I can edit the name/text etc. All non vector files should be high resolution at 1039 x 697 pixels at 300 dpi.

I also require a file as:
- Vector based PDF

Anyway questions please contact me.

Thank you

Industry/Entity Type

Landscape

Logo styles of interest
Pictorial/Combination Logo
Abstract Logo
Wordmark Logo
Lettermark Logo
Requirements
Must have
• The details that need to be included on the card:

- Use the provided Logo
- Name: Wiktor Baranowski
- Email: sales@vistalumeworks.com.au
- Website: vistalumeworks.com.au
- Twitter: twitter.com/vistalumeworks
- Facebook: facebook.com/vistalumeworks
- Mobile 0417 539 662

```html
<!DOCTYPE html>
<html lang="en">
<head>
<meta charset="utf-8">
<title>Vistalume Works – Business Cards</title>
<link rel="stylesheet" href="https://fonts.googleapis.com/css2?family=Source+Sans+3:wght@400;600;700&display=swap">
<style>
  :root {
    --stage: #1f2625;
    --card: #ffffff;
    --slate: #3d4254;
    --blue: #3f93d1;
    --ink: #3a3f4f;
    --white: #ffffff;
  }
  * { margin: 0; padding: 0; box-sizing: border-box; }
  html, body {
    width: 987px; height: 1200px; overflow: hidden;
    background: var(--stage);
    font-family: "Source Sans 3", "Myriad Pro", Arial, sans-serif;
    color: var(--ink);
  }
  .card {
    position: absolute;
    width: 789px; height: 451px;
    background: var(--card);
    border-radius: 28px;
    overflow: hidden;
  }
  .card--single { left: 97px; top: 116px; }
  .card--back   { left: 92px; top: 637px; }

  .wave { position: absolute; left: 0; top: 0; width: 789px; height: 451px; }
  .wave .band { fill: var(--slate); }
  .wave .stripe { fill: var(--blue); }

  .brand {
    position: absolute;
    display: flex; align-items: center; justify-content: center; gap: 14px;
    font-weight: 600; color: var(--slate);
    letter-spacing: 1px; text-transform: uppercase; white-space: nowrap;
  }
  .brand__dot { border-radius: 50%; background: var(--slate); flex: none; }

  .card--single .brand { left: 20px; width: 400px; top: 216px; font-size: 33px; }
  .card--single .brand__dot { width: 34px; height: 34px; }

  .card--back .brand { left: 0; width: 789px; top: 250px; font-size: 50px; }
  .card--back .brand__dot { width: 50px; height: 50px; }

  .person { position: absolute; left: 459px; top: 72px; }
  .person__name { font-size: 31px; font-weight: 700; line-height: 1; color: var(--ink); white-space: nowrap; }
  .person__role { font-size: 20px; font-weight: 400; margin-top: 5px; color: var(--ink); }

  .contacts { position: absolute; left: 456px; top: 210px; list-style: none; font-size: 20.5px; line-height: 29.5px; white-space: nowrap; }
  .contacts b { font-weight: 700; }

  .socials {
    position: absolute; left: 0; width: 789px; top: 412px;
    text-align: center; font-size: 20.5px; color: var(--white); white-space: nowrap;
  }
  .socials b { font-weight: 700; }
  .socials .sep { margin: 0 8px; }

  .site {
    position: absolute; left: 0; width: 789px; top: 396px;
    text-align: center; font-size: 27px; color: var(--ink);
  }
</style>
</head>
<body>

<section class="card card--single" aria-label="Single-sided card and front side of the double-sided card, carrying all contact details">
  <svg class="wave" viewBox="0 0 789 451" aria-hidden="true">
    <path class="band" d="M0 368 C90 342 200 324 300 330 C420 338 520 400 620 400 C700 400 750 376 789 356 L789 451 L0 451 Z"/>
    <path class="stripe" d="M165 320 C300 318 420 358 540 372 C640 384 720 352 789 318 L789 338 C720 370 640 394 540 384 C420 372 300 330 165 320 Z"/>
  </svg>

  <div class="brand"><span class="brand__dot"></span><span>Vistalume Works</span></div>

  <div class="person">
    <p class="person__name">Wiktor Baranowski</p>
    <p class="person__role">Administrator</p>
  </div>

  <ul class="contacts">
    <li><b>m</b> : 0417 539 662</li>
    <li><b>e</b> : sales@vistalumeworks.com.au</li>
    <li><b>w</b> : vistalumeworks.com.au</li>
  </ul>

  <p class="socials"><b>t</b> : twitter.com/vistalumeworks<span class="sep">|</span><b>f</b> : facebook.com/vistalumeworks</p>
</section>

<section class="card card--back" aria-label="Back side of the double-sided card">
  <div class="brand"><span class="brand__dot"></span><span>Vistalume Works</span></div>
  <p class="site">www.vistalumeworks.com.au</p>
</section>

</body>
</html>
```